Women's Jewellery startup needs a captivating, beautifully designed and intuitive online store

[12/24 update]

Added 2 additional documents:

Feedback on designs received so far: designer feedback.docx
Product images from catalogue: products images.docx

Please read the feedback provided on designs provided so far to guide you further on your submission. The product images can be used to create promotional banners for the site.

@@@Added a document (VELISTO JEWELLERY_checklist.docx) which can be used by designers as a checklist when submitting their designs to ensure all aspects of the requirements have been covered @@@

+++IMPORTANT BUT NOT SPECIFIED IN THE REQUIREMENTS DOCUMENT - DESIGN SHOULD INCLUDE SUPPORT FOR MOBILE FRIENDLY SITE TOO+++

***Previous experience designing Jewellery online stores preferred (not essential)***

The name of the online Jewellery store is "Velisto Jewellery" and the business is based in Hong Kong. It will be run by 2 stay at home mothers. We need a Shopify themed store designed that will achieve the following objectives in order of priority:

• Conversion: The primary objective of the design/content is to prompt the customer to make a purchase. While this may sound obvious, it is mentioned so as not to distract the design process by focusing on other objectives (which are also important). The site also needs to be optimized so as to rank high in search engine searches for relevant keywords (SEO)
• Navigation: An intuitive interface which takes away a lot of the thinking from the customer by making it obvious what they need to do when they visit the store
• Engagement: Encourages the customer to spend time on the website and share content with their social network

Where applicable, the design of the store should reflect as closely as possible the mission statements and words outlined below:

• Jewellery you’ll fall in love with
• We want every client to leave the store with a smile
• We want to be able to provide the best service we can in every situation no matter what
• We aim to increase our business by word of mouth; therefore we tell people things about our store that makes it interesting for them to share
• We love every customer, no matter how difficult things get
• We, as a team, are so well informed about our products and brands that we always have the best information for our customers
• We celebrate women here!
• We celebrate life in here!
• We celebrate beauty here!
• We celebrate families here, as jewellery often stays within families.
• We will always try to make an extra step
• We will always try to exceed the expectation of our customers
• We will go as far as we possibly can to attract a customer back to our store and connect with us
• Every client that leaves our store knows more about jewellery because we passionately told him about it
• Romantic, classic, love, warm, cool, stylish

A draft functional specification is attached with this brief. We would like the design to reflect as closely as possible the functional requirements outlined in the document. Open to suggestions to improve upon the functional requirements.

Target Market(s)

Women aged 18-55

Industry/Entity Type

Jewelry Store

Coding

Coded - Design and coding required

Number of Pages Required

5+ page

Font styles to use
Other font styles liked:
• Myriad Pro as per Logo but open to any font that complements this one

Requirements
Must have
• 1. A look that encourages the user to make a purchase
• 2. An intuitive, easy to navigate and engaging interface
• 3. Primary colour scheme as defined in the functional specification attached
• 4. Simplistic look, not too cluttered
Nice to have
• 1. Closely matching the functional requirements of the site as outlined in the requirements specification but open to any better ideas

```html
<!DOCTYPE html>
<html lang="en">
<head>
<meta charset="utf-8">
<title>Velisto Jewellery – Store</title>
<link href="https://fonts.googleapis.com/css2?family=Source+Sans+3:wght@300;400;600;700&display=swap" rel="stylesheet">
<style>
:root{
  --gold:#c9973f;
  --gold-deep:#b5842f;
  --ink:#2a2a2a;
  --muted:#9a9a9a;
  --line:#dedede;
  --page:#ffffff;
  --card:#f4f4f4;
  --dark:#2f2f2f;
  --darker:#262626;
  --btn-dark:#3a3a3a;
  --skin:#e6c3a6;
  --skin-deep:#b98463;
  --night:#0c0a09;
}
*{box-sizing:border-box;margin:0;padding:0}
html,body{width:811px;height:1200px;overflow:hidden}
body{position:relative;font-family:"Source Sans 3",sans-serif;background:var(--page);color:var(--ink)}
.abs{position:absolute}

.promo-bar{left:0;top:0;width:811px;height:21px;background:var(--gold);color:#fff;font-size:9px;text-align:center;line-height:21px}
.util-bar{left:0;top:21px;width:811px;height:24px;background:#1e1e1e;color:#ddd;font-size:8.5px}
.util-bar .links{position:absolute;right:72px;top:0;line-height:24px;display:flex;gap:5px;align-items:center}
.util-bar .cart-count{display:inline-block;width:12px;height:12px;border-radius:50%;background:#333;text-align:center;line-height:12px;font-size:7px}

.brand{left:66px;top:52px;width:100px;text-align:center}
.brand .mark{display:block;width:26px;height:26px;border:1.5px solid var(--gold);margin:0 auto 5px}
.brand .name{font-size:10px;letter-spacing:3px;color:var(--gold-deep)}
.brand .tag{font-size:7px;color:#444;margin-top:2px;white-space:nowrap}
.main-nav{top:74px;left:0;font-size:10.5px;color:#222}
.main-nav span{position:absolute;white-space:nowrap}

.hero{left:66px;top:122px;width:678px;height:268px;
  background:
    radial-gradient(ellipse 120px 160px at 70px 150px,rgba(235,210,190,.55),transparent 70%),
    radial-gradient(ellipse 260px 140px at 560px 70px,rgba(150,110,50,.22),transparent 70%),
    linear-gradient(90deg,#8a6a58 0%,#4a3328 18%,#1d1512 38%,var(--night) 62%,#15110d 100%)}
.dots{top:400px;left:390px;display:flex;gap:8px}
.dots i{width:4px;height:4px;border-radius:50%;background:#555}

.offer{top:414px;height:120px;display:flex;flex-direction:column;justify-content:center;align-items:center;padding-left:96px;text-align:center}
.offer .big{font-size:18px;font-weight:700;color:var(--gold);line-height:20px}
.offer .small{font-size:8.5px;line-height:14px;margin-top:3px;width:116px}
.offer-a{left:66px;width:212px;color:#333;
  background:radial-gradient(ellipse 70px 60px at 60px 55px,#fbf3f1,transparent 75%),linear-gradient(120deg,#e9c5c2 0%,#f3dcd9 50%,#f8ecea 100%)}
.offer-b{left:299px;width:211px;color:#eee;
  background:radial-gradient(ellipse 90px 70px at 60px 50px,#8b7a55,transparent 75%),linear-gradient(110deg,#4a4a52 0%,#6b5530 45%,#4a3518 100%)}
.offer-c{left:534px;width:210px;color:#eee;
  background:radial-gradient(ellipse 70px 60px at 70px 70px,#9a9a9a,transparent 75%),linear-gradient(110deg,#3d3d3d 0%,#5a5a5a 40%,#2f2f2f 100%)}

.rule{left:66px;width:678px;height:1px;background:var(--line)}
.filter label{position:absolute;top:553px;font-size:9px;color:#666}
.select{position:absolute;height:19px;border:1px solid #d4d4d4;background:#fafafa;font-size:8.5px;font-weight:600;color:#333;line-height:17px;padding-left:8px}
.select svg{position:absolute;right:7px;top:6px}
.section-title{left:66px;top:608px;font-size:19px;font-weight:400;color:#333}
.pager{left:717px;top:610px}

.product{top:642px;width:156px;height:300px;background:var(--card);border:1px solid #ececec}
.product .photo{position:absolute;left:0;top:0;width:154px;height:175px}
.product .wish{position:absolute;left:0;top:125px;width:154px;text-align:center;font-size:7px;color:#444}
.product .wish svg{display:block;margin:4px auto 0}
.product h3{position:absolute;left:10px;top:185px;font-size:11.5px;font-weight:400;color:#333}
.product .plate{position:absolute;left:10px;top:203px;font-size:7.5px;color:var(--muted)}
.product .desc{position:absolute;left:10px;top:220px;width:136px;font-size:7px;line-height:10px;color:#444;text-align:justify}
.product .price{position:absolute;left:10px;top:255px;font-size:10px;font-weight:600;color:#222}
.btn{position:absolute;top:271px;height:17px;line-height:17px;font-size:7.5px;font-weight:700;color:#fff;text-align:center}
.btn-cart{left:11px;width:64px;background:var(--gold)}
.btn-view{left:79px;width:66px;background:var(--btn-dark)}

.footer{left:0;top:957px;width:811px;height:152px;background:var(--dark);color:#ddd}
.footer h4{position:absolute;top:27px;font-size:10px;font-weight:700;letter-spacing:.3px;color:#eee}
.footer ul{position:absolute;top:53px;list-style:none;font-size:8.5px}
.footer li{height:18px;padding-left:16px;position:relative}
.footer li::before{content:"›";position:absolute;left:0;top:-2px;font-size:10px}
.social{position:absolute;left:482px;font-size:8.5px;display:flex;align-items:center;gap:8px}
.social i{width:19px;height:19px;border-radius:50%;display:block}
.news-input{left:606px;top:56px;width:110px;height:19px;background:#fff;color:#555;font-size:8px;line-height:19px;padding-left:26px}
.news-go{left:716px;top:56px;width:28px;height:19px;background:var(--gold)}
.legal{left:0;top:1109px;width:811px;height:91px;background:var(--darker);color:#ccc}
.cards{position:absolute;left:337px;top:24px;display:flex;gap:6px}
.cards span{width:30px;height:16px;border-radius:2px;background:#e9e9e9;color:#333;font-size:6px;font-weight:700;text-align:center;line-height:16px}
.legal p{position:absolute;top:59px;width:811px;text-align:center;font-size:8px}

.scrim{left:0;top:0;width:811px;height:1200px;background:rgba(0,0,0,.36)}
.modal{left:158px;top:171px;width:495px;height:189px;background:#fff}
.modal .visual{position:absolute;left:0;top:0;width:297px;height:189px;
  background:
    radial-gradient(ellipse 120px 110px at 170px 90px,var(--skin),transparent 75%),
    radial-gradient(ellipse 90px 70px at 90px 30px,rgba(215,180,120,.9),transparent 75%),
    linear-gradient(90deg,#2b211c 0%,var(--skin-deep) 35%,#c99778 60%,#3a2a22 88%,var(--night) 100%)}
.modal h2{position:absolute;left:297px;top:43px;width:198px;text-align:center;font-size:17px;font-weight:700;color:#111;line-height:21px}
.modal h2 span{display:block;font-weight:300}
.modal .email{position:absolute;left:320px;top:101px;width:157px;height:21px;background:#f1f1f1;border:1px solid #ddd;font-size:6.5px;line-height:19px;padding-left:8px;color:#222}
.modal .go{position:absolute;left:352px;top:135px;width:84px;height:22px;background:var(--gold);color:#fff;font-size:10.5px;font-weight:700;text-align:center;line-height:22px;letter-spacing:.4px}
.close{left:640px;top:166px;width:18px;height:18px;border-radius:50%;background:var(--gold);color:#fff;font-size:9px;text-align:center;line-height:18px}
</style>
</head>
<body>

<div class="abs promo-bar">Free shipping on all orders over $50</div>
<div class="abs util-bar">
  <div class="links">Sign in / Wishlist / HKD
    <svg width="6" height="4" viewBox="0 0 6 4"><path d="M0 0L3 3L6 0" fill="none" stroke="#ccc"/></svg>
    / My Account /
    <svg width="10" height="8" viewBox="0 0 10 8"><path d="M0 1h2l1 5h6l1-4H3" fill="none" stroke="#ddd"/></svg>
    <span class="cart-count">0</span> /
    <svg width="9" height="9" viewBox="0 0 9 9"><circle cx="3.5" cy="3.5" r="2.7" fill="none" stroke="#ddd" stroke-width="1.3"/><path d="M5.5 5.5L8.5 8.5" stroke="#ddd" stroke-width="1.3"/></svg>
  </div>
</div>

<div class="abs brand">
  <span class="mark"></span>
  <div class="name">VELISTO</div>
  <div class="tag">Jewellery you'll fall in love with</div>
</div>
<nav class="abs main-nav">
  <span style="left:512px">Home</span><span style="left:559px">Shop</span><span style="left:602px">Blog</span><span style="left:644px">About Us</span><span style="left:705px">Contact</span>
</nav>

<div class="abs hero" role="img" aria-label="Hero photograph of a model wearing a diamond necklace, earrings and rings against a black backdrop with faint gold damask"></div>
<div class="abs dots"><i></i><i></i><i></i></div>

<div class="abs offer offer-a" role="img" aria-label="Diamond solitaire ring on soft pink fabric"><div class="big">Extra 10%</div><div class="small">off Diamond rings till March 31st, 2018</div></div>
<div class="abs offer offer-b" role="img" aria-label="Gold jewellery set with blue stones"><div class="big">Extra 20%</div><div class="small">off Gold sed do eiusmod tempor</div></div>
<div class="abs offer offer-c" role="img" aria-label="Silver cuff bracelets, chains and rings"><div class="big">Extra 40%</div><div class="small">off Silver consectetur adipiscing elit</div></div>

<div class="abs rule" style="top:545px"></div>
<div class="filter">
  <label style="left:66px">Type</label><label style="left:178px">Collection</label><label style="left:288px">Metal</label><label style="left:406px">Gemstone</label><label style="left:523px">Price Range</label><label style="left:635px">Sort By</label>
  <div class="select" style="left:66px;top:570px;width:86px">Ring<svg width="6" height="4"><path d="M0 0L3 3L6 0" fill="none" stroke="#444"/></svg></div>
  <div class="select" style="left:178px;top:570px;width:86px">Select<svg width="6" height="4"><path d="M0 0L3 3L6 0" fill="none" stroke="#444"/></svg></div>
  <div class="select" style="left:288px;top:570px;width:92px">10% Rose Gold<svg width="6" height="4"><path d="M0 0L3 3L6 0" fill="none" stroke="#444"/></svg></div>
  <div class="select" style="left:406px;top:570px;width:85px">Amethyst<svg width="6" height="4"><path d="M0 0L3 3L6 0" fill="none" stroke="#444"/></svg></div>
  <div class="select" style="left:523px;top:570px;width:85px">High to low<svg width="6" height="4"><path d="M0 0L3 3L6 0" fill="none" stroke="#444"/></svg></div>
  <div class="select" style="left:635px;top:570px;width:109px">Our Favourite<svg width="6" height="4"><path d="M0 0L3 3L6 0" fill="none" stroke="#444"/></svg></div>
</div>
<div class="abs rule" style="top:599px"></div>

<h2 class="abs section-title">Top Products</h2>
<div class="select" style="left:600px;top:606px;width:109px">What's new<svg width="6" height="4"><path d="M0 0L3 3L6 0" fill="none" stroke="#444"/></svg></div>
<svg class="abs pager" width="18" height="12" viewBox="0 0 18 12"><path d="M5 2L1 6L5 10M13 2L17 6L13 10" fill="none" stroke="#333" stroke-width="1.3"/></svg>

<article class="abs product" style="left:66px">
  <div class="photo" role="img" aria-label="Sapphire ring with gold halo on white" style="background:radial-gradient(ellipse 60px 70px at 77px 80px,#e3e6ee,#fff 80%)"></div>
  <div class="wish">Wishlist<svg width="11" height="10" viewBox="0 0 12 11"><path d="M6 10L1.3 5.3A2.8 2.8 0 0 1 6 1.8A2.8 2.8 0 0 1 10.7 5.3Z" fill="none" stroke="#333"/></svg></div>
  <h3>Diamond Ring</h3><div class="plate">Silver plated</div>
  <p class="desc">Neque porro quisquam est qui dolorem ipsum quia dolor sit amet,</p>
  <div class="price">$29.00 CAD</div><div class="btn btn-cart">ADD TO CART</div><div class="btn btn-view">QUICK VIEW</div>
</article>
<article class="abs product" style="left:240px">
  <div class="photo" role="img" aria-label="Emerald cut green stone ring on white" style="background:radial-gradient(ellipse 60px 70px at 77px 80px,#e2ece4,#fff 80%)"></div>
  <div class="wish">Wishlist<svg width="11" height="10" viewBox="0 0 12 11"><path d="M6 10L1.3 5.3A2.8 2.8 0 0 1 6 1.8A2.8 2.8 0 0 1 10.7 5.3Z" fill="none" stroke="#333"/></svg></div>
  <h3>Diamond Ring</h3><div class="plate">Silver plated</div>
  <p class="desc">Neque porro quisquam est qui dolorem ipsum quia dolor sit amet,</p>
  <div class="price">$29.00 CAD</div><div class="btn btn-cart">ADD TO CART</div><div class="btn btn-view">QUICK VIEW</div>
</article>
<article class="abs product" style="left:414px">
  <div class="photo" role="img" aria-label="Silver band ring set with green stones on white" style="background:radial-gradient(ellipse 60px 40px at 77px 80px,#e3ece5,#fff 80%)"></div>
  <div class="wish">Wishlist<svg width="11" height="10" viewBox="0 0 12 11"><path d="M6 10L1.3 5.3A2.8 2.8 0 0 1 6 1.8A2.8 2.8 0 0 1 10.7 5.3Z" fill="#d8333b"/></svg></div>
  <h3>Diamond Ring</h3><div class="plate">Silver plated</div>
  <p class="desc">Neque porro quisquam est qui dolorem ipsum quia dolor sit amet,</p>
  <div class="price">$29.00 CAD</div><div class="btn btn-cart">ADD TO CART</div><div class="btn btn-view">QUICK VIEW</div>
</article>
<article class="abs product" style="left:589px">
  <div class="photo" role="img" aria-label="Diamond ring with blue stone accents on white" style="background:radial-gradient(ellipse 60px 70px at 77px 80px,#e4e6f0,#fff 80%)"></div>
  <div class="wish">Wishlist<svg width="11" height="10" viewBox="0 0 12 11"><path d="M6 10L1.3 5.3A2.8 2.8 0 0 1 6 1.8A2.8 2.8 0 0 1 10.7 5.3Z" fill="none" stroke="#333"/></svg></div>
  <h3>Diamond Ring</h3><div class="plate">Silver plated</div>
  <p class="desc">Neque porro quisquam est qui dolorem ipsum quia dolor sit amet,</p>
  <div class="price">$29.00 CAD</div><div class="btn btn-cart">ADD TO CART</div><div class="btn btn-view">QUICK VIEW</div>
</article>

<footer class="abs footer">
  <h4 style="left:67px">ABOUT US</h4>
  <ul style="left:67px"><li>Our Story</li><li>Wholesale inquiries</li></ul>
  <h4 style="left:213px">SHOPPING</h4>
  <ul style="left:213px"><li>Orders</li><li>Wishlist</li><li>Size Guide</li></ul>
  <h4 style="left:336px">CUSTOMER CARE</h4>
  <ul style="left:336px"><li>Returns</li><li>FAQs</li><li>Care &amp; Warranty</li><li>Contact Us</li></ul>
  <h4 style="left:485px">SOCIAL LINKS</h4>
  <div class="social" style="top:54px"><i style="background:#3b5998"></i>Circlebook</div>
  <div class="social" style="top:81px"><i style="background:#b5842f"></i>snapframe</div>
  <div class="social" style="top:107px"><i style="background:#c8232c"></i>Pinboardly</div>
  <h4 style="left:606px">NEWSLETTER</h4>
  <div class="abs news-input">Email address
    <svg style="position:absolute;left:9px;top:6px" width="10" height="7" viewBox="0 0 10 7"><rect x=".5" y=".5" width="9" height="6" fill="none" stroke="#444"/><path d="M.5 .5L5 4L9.5 .5" fill="none" stroke="#444"/></svg></div>
  <div class="abs news-go"><svg style="position:absolute;left:9px;top:5px" width="10" height="9" viewBox="0 0 10 9"><path d="M0 4.5H8M5 1L8.5 4.5L5 8" fill="none" stroke="#fff" stroke-width="1.6"/></svg></div>
</footer>
<div class="abs legal">
  <div class="cards"><span>Payvo</span><span>Cardix</span><span>Findo</span><span>Amara</span></div>
  <p>© 2017 | www.velistostore.com</p>
</div>

<div class="abs scrim"></div>
<section class="abs modal">
  <div class="visual" role="img" aria-label="Close-up beauty photograph of a blonde model wearing a small earring"></div>
  <h2>SUBSCRIBE<span>NEWSLETTER</span></h2>
  <div class="email">Enter Email Id</div>
  <div class="go">SUBSCRIBE</div>
</section>
<div class="abs close">X</div>

</body>
</html>
```